Graphic Design for a 3 Banner Tradeshow Setup

We are a Pipe Restoration company that specializes in trenchless pipelining. We need a design for a 3 banner setup to use at tradeshows. See attached "banner specs" for sizing - note the 48" x 92" will be in between the two 36" x 92" banners. See attached "Mock-Up" of information each banner needs and utilize the color scheme of the banners we already have in the "both DWM banners" AI file attached. The final designs should communicate what we do and attract people into our booth. We would like to have graphics of realistic pipes for a before (dirty pipe), after cleaning pipe, and lined pipe - see example of "pipe pictures" attached. I'm not sure if this is something you can generate or if we will need to find images of our own to send. Also, see attached "screenshot-process" to see similar images we would like to use to showcase the process.
Target Market(s)
Homeowners, Property Managers, HOA Communities, Healthcare Facilities & Hospitals, and commercial properties
Industry/Entity Type
Trenchless Pipelining
Look and feel

```html
<!DOCTYPE html>
<html lang="en">
<head>
<meta charset="utf-8">
<title>DWM Tradeshow Banner Set</title>
<link href="https://fonts.googleapis.com/css2?family=Krona+One&family=Barlow:wght@500;600&family=Barlow+Semi+Condensed:wght@600;700&display=swap" rel="stylesheet">
<style>
:root{
  --navy:#0c1730;
  --navy-deep:#07101f;
  --blue:#1d5fb0;
  --blue-dark:#163f86;
  --sky:#1ea0e6;
  --ice:#eaf4fb;
  --ice-2:#cfe6f5;
  --ink:#0d1426;
  --white:#ffffff;
  --stage:#e3e3e5;
}
*{box-sizing:border-box;margin:0;padding:0}
ul,ol{list-style:none}
html,body{width:1200px;height:900px;overflow:hidden;background:var(--stage)}
.stage{position:relative;width:1200px;height:900px}
.banner{position:absolute;top:90px;height:720px;overflow:hidden}
.banner--side{width:282px;background:linear-gradient(180deg,var(--navy) 0%,var(--navy) 45%,var(--blue-dark) 75%,var(--sky) 100%)}
.banner--left{left:90px}
.banner--right{left:828px}
.banner--center{left:412px;width:376px;background:var(--white)}

.brand{position:absolute;top:34px;left:0;right:0;text-align:center;color:var(--white)}
.brand-row{display:flex;align-items:center;justify-content:center;gap:10px}
.brand-mark{width:34px;height:34px;background:var(--blue);border-radius:4px}
.brand-name{font-family:'Krona One',sans-serif;font-size:42px;letter-spacing:2px;line-height:1}
.brand-sub{font-family:'Krona One',sans-serif;font-size:8px;letter-spacing:2.4px;margin-top:8px}

.panel{position:absolute;left:22px;right:22px;top:128px;height:440px;border-radius:14px;
  background:radial-gradient(ellipse at 60% 40%,var(--white) 0%,var(--ice) 50%,var(--ice-2) 100%);
  border:2px solid #5aa8e0}
.panel-tab{position:absolute;top:-10px;left:50%;transform:translateX(-50%);width:168px;height:34px;
  background:linear-gradient(180deg,var(--blue),var(--blue-dark));border-radius:0 0 18px 18px;
  color:var(--white);font-family:'Krona One',sans-serif;font-size:13px;display:flex;align-items:center;justify-content:center}

.assess-list{position:absolute;top:40px;left:0;right:0;display:flex;flex-direction:column;align-items:center;gap:14px}
.assess-item{text-align:center}
.icon-tile{width:52px;height:52px;border-radius:6px;background:linear-gradient(160deg,var(--sky),var(--blue-dark));
  display:flex;align-items:center;justify-content:center;margin:0 auto 6px;box-shadow:0 2px 3px rgba(0,0,0,.25)}
.item-label{font-family:'Krona One',sans-serif;font-size:11.5px;line-height:1.2;color:var(--ink)}

.fix-list{position:absolute;top:42px;left:16px;right:10px;display:flex;flex-direction:column;gap:13px}
.fix-item{display:flex;align-items:center;gap:12px}
.fix-item .icon-tile{margin:0;flex:none}
.fix-item .item-label{font-size:12.5px}

.photo{position:absolute;left:0;right:0;bottom:0;height:140px}
.photo--control{background:linear-gradient(160deg,#2f4a7a,#1c2f5e 50%,#3558b5)}
.photo--crew{background:linear-gradient(160deg,#3e5a3a,#2b3b30 50%,#4d6b46)}

.before-after{position:absolute;top:18px;left:40px;right:40px;height:110px;display:flex;justify-content:space-between}
.pipe-shot{width:140px;height:100px;border-radius:50%;display:flex;align-items:center;justify-content:center;
  font-family:'Krona One',sans-serif;font-size:9px;color:var(--white)}
.pipe-shot--before{background:radial-gradient(circle,#1a0f0c 30%,#6e4a3a 70%,#9a7a68)}
.pipe-shot--after{background:radial-gradient(circle,#0f5f78 30%,#5cc6e6 62%,#6e4a3a 78%)}

.headline{position:absolute;left:0;right:0;text-align:center;font-family:'Krona One',sans-serif;
  background:linear-gradient(180deg,var(--blue-dark),var(--sky));-webkit-background-clip:text;background-clip:text;color:transparent}
.headline--pipe{top:128px;font-size:72px;line-height:1}
.headline--problems{top:208px;font-size:28px;line-height:1}

.promise{position:absolute;top:256px;left:0;right:0;height:100px;background:linear-gradient(180deg,var(--blue-dark),var(--sky));
  color:var(--white);text-align:center;padding-top:16px}
.promise-lead{font-family:'Krona One',sans-serif;font-size:10.5px}
.promise-main{font-family:'Krona One',sans-serif;font-size:17px;line-height:1.3;margin-top:6px}

.process{position:absolute;top:372px;left:14px;right:14px;display:grid;grid-template-columns:1fr 1fr;column-gap:14px;row-gap:12px}
.step{position:relative}
.step-art{height:56px;margin-left:14px;border-radius:4px;background:linear-gradient(180deg,#8a8f98,#5c4a3a 60%,#7a8088)}
.step-art--lined{background:linear-gradient(180deg,#8a8f98,#2a8fd8 50%,#7a8088)}
.step-art--finished{background:linear-gradient(180deg,#3aa7ee,#1d5fb0)}
.step-num{position:absolute;left:0;top:18px;width:26px;height:26px;border-radius:50%;background:var(--blue);border:2px solid var(--white);
  box-shadow:0 0 0 2px var(--blue-dark);color:var(--white);font-family:'Krona One',sans-serif;font-size:12px;display:flex;align-items:center;justify-content:center}
.step-text{font-family:'Barlow',sans-serif;font-weight:500;font-size:10.5px;line-height:1.3;color:var(--ink);margin:8px 0 0 14px}

.cta{position:absolute;left:16px;right:16px;bottom:0;height:92px;border-radius:12px 12px 0 0;
  background:linear-gradient(180deg,var(--white) 0%,#222 25%,var(--navy-deep));text-align:center}
.cta-tab{position:absolute;top:-10px;left:20px;right:20px;height:22px;background:var(--sky);border-radius:3px;
  color:var(--white);font-family:'Barlow Semi Condensed',sans-serif;font-weight:700;font-size:12.5px;display:flex;align-items:center;justify-content:center}
.cta-web{margin-top:24px;font-family:'Krona One',sans-serif;font-size:13px;color:var(--sky)}
.cta-phone{margin-top:8px;font-family:'Krona One',sans-serif;font-size:20px;color:var(--white)}
svg{display:block}
</style>
</head>
<body>
<main class="stage">

  <section class="banner banner--side banner--left">
    <header class="brand">
      <div class="brand-row"><span class="brand-mark"></span><span class="brand-name">DWM</span></div>
      <div class="brand-sub">DRAIN WORKS MANAGEMENT</div>
    </header>
    <div class="panel">
      <div class="panel-tab">WE ASSESS</div>
      <ul class="assess-list">
        <li class="assess-item">
          <div class="icon-tile"><svg width="30" height="30" viewBox="0 0 30 30" fill="none" stroke="#fff" stroke-width="2"><rect x="4" y="6" width="9" height="12" rx="2"/><path d="M8 18v7M19 5v18a3 3 0 0 0 6 0V5z"/></svg></div>
          <div class="item-label">CCTV PIPE<br>INVESTIGATION</div>
        </li>
        <li class="assess-item">
          <div class="icon-tile"><svg width="30" height="30" viewBox="0 0 30 30" fill="none" stroke="#fff" stroke-width="2"><path d="M3 11l6-3 6 4 6-4 6 3v7l-7 5-5-4-5 4-7-5z"/></svg></div>
          <div class="item-label">SCOPE<br>DEVELOPMENT</div>
        </li>
        <li class="assess-item">
          <div class="icon-tile"><svg width="30" height="30" viewBox="0 0 30 30" fill="none" stroke="#fff" stroke-width="2"><rect x="6" y="3" width="15" height="23" rx="2"/><rect x="9" y="6" width="9" height="4"/><circle cx="22" cy="19" r="5"/></svg></div>
          <div class="item-label">BUDGETARY<br>EVALUATION</div>
        </li>
        <li class="assess-item">
          <div class="icon-tile"><svg width="30" height="30" viewBox="0 0 30 30" fill="none" stroke="#fff" stroke-width="2"><circle cx="16" cy="13" r="8"/><path d="M10 19l-7 7"/></svg></div>
          <div class="item-label">PROJECT<br>OVERSIGHT</div>
        </li>
      </ul>
    </div>
    <div class="photo photo--control" role="img" aria-label="Technician at a control desk reviewing sewer camera footage on several monitors"></div>
  </section>

  <section class="banner banner--center">
    <div class="before-after">
      <div class="pipe-shot pipe-shot--before" role="img" aria-label="Corroded pipe before restoration">BEFORE</div>
      <div class="pipe-shot pipe-shot--after" role="img" aria-label="Pipe with new blue liner after restoration">AFTER</div>
    </div>
    <h1 class="headline headline--pipe">PIPE</h1>
    <h2 class="headline headline--problems">PROBLEMS?</h2>
    <div class="promise">
      <p class="promise-lead">WE HELP FIX PIPE PROBLEMS</p>
      <p class="promise-main">WITHOUT HAVING TO<br>TEAR UP YOUR BUIDLING</p>
    </div>
    <ol class="process">
      <li class="step">
        <div class="step-art" role="img" aria-label="Cutaway of a pipe blocked by debris and roots"></div>
        <span class="step-num">1</span>
        <p class="step-text">A sewer camera reveals a blocked brenched and or root interupted pipe</p>
      </li>
      <li class="step">
        <div class="step-art step-art--lined" role="img" aria-label="Cutaway of a liner being pulled into a pipe"></div>
        <span class="step-num">3</span>
        <p class="step-text">A CIPP Liner is pulled into place and the bladder inflated.</p>
      </li>
      <li class="step">
        <div class="step-art" role="img" aria-label="Cutaway of a cutting tool cleaning a pipe"></div>
        <span class="step-num">2</span>
        <p class="step-text">The pipe is cleaned with a scropion cutting tool</p>
      </li>
      <li class="step">
        <div class="step-art step-art--finished" role="img" aria-label="Cutaway of a finished lined pipe"></div>
        <span class="step-num">4</span>
        <p class="step-text">After curing the bladder is removed leaving behind a structrial pipe within a pipe</p>
      </li>
    </ol>
    <div class="cta">
      <div class="cta-tab">CALL TODAY FOR ALL YOUR PIPE RESTORATION</div>
      <p class="cta-web">WWW.DWMPIPE.COM</p>
      <p class="cta-phone">1-800-555-0142</p>
    </div>
  </section>

  <section class="banner banner--side banner--right">
    <header class="brand">
      <div class="brand-row"><span class="brand-mark"></span><span class="brand-name">DWM</span></div>
      <div class="brand-sub">DRAIN WORKS MANAGEMENT</div>
    </header>
    <div class="panel">
      <div class="panel-tab">WE FIX</div>
      <ul class="fix-list">
        <li class="fix-item"><div class="icon-tile"><svg width="30" height="30" viewBox="0 0 30 30" fill="none" stroke="#fff" stroke-width="2"><path d="M6 4v12a8 8 0 0 0 16 0v-4h4"/></svg></div><div class="item-label">SLOW<br>DRAINS</div></li>
        <li class="fix-item"><div class="icon-tile"><svg width="30" height="30" viewBox="0 0 30 30" fill="none" stroke="#fff" stroke-width="2"><path d="M4 20q4-3 8 0t8 0 8 0M4 25q4-3 8 0t8 0 8 0M8 4v12M20 6q5 2 4 10"/></svg></div><div class="item-label">WATER<br>BACK - UPS</div></li>
        <li class="fix-item"><div class="icon-tile"><svg width="30" height="30" viewBox="0 0 30 30" fill="none" stroke="#fff" stroke-width="2"><path d="M10 4q-3 3 0 6t0 6M15 4q-3 3 0 6t0 6M20 4q-3 3 0 6t0 6"/><ellipse cx="15" cy="22" rx="11" ry="4"/></svg></div><div class="item-label">SEWER<br>ODORS</div></li>
        <li class="fix-item"><div class="icon-tile"><svg width="30" height="30" viewBox="0 0 30 30" fill="none" stroke="#fff" stroke-width="2"><path d="M3 11h24M3 17h24M3 8v12M27 8v12M15 11l-2 3 2 3"/></svg></div><div class="item-label">CRACKED<br>PIPES</div></li>
        <li class="fix-item"><div class="icon-tile"><svg width="30" height="30" viewBox="0 0 30 30" fill="none" stroke="#fff" stroke-width="2"><path d="M15 4v22M15 10q-5-4-8 0M15 10q5-4 8 0M3 20h24"/></svg></div><div class="item-label">ROOT<br>INTRUSION</div></li>
        <li class="fix-item"><div class="icon-tile"><svg width="30" height="30" viewBox="0 0 30 30" fill="none" stroke="#fff" stroke-width="2"><path d="M4 6h16v6M20 12v4M6 26l16-10"/><circle cx="24" cy="14" r="3"/></svg></div><div class="item-label">RECURRING<br>PLUMBING<br>PROBLEMS</div></li>
      </ul>
    </div>
    <div class="photo photo--crew" role="img" aria-label="Crew member in a company shirt operating a green hose reel outdoors"></div>
  </section>

</main>
</body>
</html>
```